Website for virtual assistant and proofreader

Professional, feminine (but not flowery!) website offering and explaining my services as a VA and Proofreader. Probably only 7 pages: home, about, services (x2), fees, testimonials and contact page. <br/><br/>I already have most of the content, which I have uploaded so you can get an idea of waht I do. I have brand colours and logo already also uploaded. I really just need the bones of the site to be designed and am happy/capable of setting this up as a Wordpress site. I'm just rubbish at design!

Industry/Entity Type

Business Service

Coding

Coded - Design and coding required

Number of Pages Required

4 page

Other font styles liked:
• Roboto Bold + Great Vibes

Colors
3276b5
fee3d4

Requirements
Must have
• should be informative, professional, feminine. Clean, clear, CTA's links to services and fees pages
• Also, see all 3 colour codes on the attached doc.
Nice to have
• business images but place holders will do
Should not have
• Nothing flowery or cartoons! Not 'busy'

```html
<!DOCTYPE html>
<html lang="en">
<head>
<meta charset="utf-8">
<title>Clara M Whitfield – Virtual Assistant and Proofreader</title>
<link href="https://fonts.googleapis.com/css2?family=Roboto:wght@400;500;700;900&family=Great+Vibes&display=swap" rel="stylesheet">
<style>
:root{
  --navy:#1d4c7c;
  --navy-dark:#163a60;
  --navy-deep:#12304f;
  --peach:#ebb6a2;
  --peach-light:#fee3d4;
  --blush:#f8ede7;
  --lavender:#f1f0f8;
  --ink:#2c2c2c;
  --muted:#555;
  --white:#fff;
  --night:#15181f;
}
*{box-sizing:border-box;margin:0;padding:0}
html,body{width:1200px;height:5300px;overflow:hidden}
body{position:relative;font-family:'Roboto',sans-serif;color:var(--ink);background:var(--white)}
.abs{position:absolute}
.btn{position:absolute;display:flex;align-items:center;justify-content:center;font-weight:700;font-size:15px;letter-spacing:.3px;color:var(--white);text-transform:uppercase}
.btn--navy{background:var(--navy)}
.btn--peach{background:var(--peach);color:var(--navy-deep)}
.section-title{position:absolute;left:0;width:1200px;text-align:center;font-weight:700;font-size:38px;text-transform:uppercase;letter-spacing:.5px}
.section-title::after{content:"";display:block;width:82px;height:4px;background:currentColor;margin:14px auto 0;opacity:.9}

/* top bar */
.topbar{left:0;top:0;width:1200px;height:30px;background:var(--peach);font-size:15px;color:var(--navy-deep)}
.topbar__item{position:absolute;top:5px;display:flex;align-items:center;gap:10px}
.nav{left:0;top:30px;width:1200px;height:98px;background:var(--white)}
.brand{left:134px;top:18px;display:flex;align-items:center;gap:12px}
.brand__mark{width:46px;height:46px;border-radius:50%;background:var(--navy)}
.brand__name{font-weight:500;font-size:19px;color:var(--navy)}
.brand__tag{font-size:11px;color:var(--muted);margin-top:3px}
.nav__links{right:140px;top:42px;display:flex;gap:30px;font-weight:500;font-size:15.5px;text-transform:uppercase;color:var(--ink)}
.nav__links .is-active{color:var(--navy)}

/* hero */
.hero{left:0;top:128px;width:1200px;height:617px;background:linear-gradient(120deg,#c9985d 0%,#8d6a49 30%,#4a3d36 60%,#2d2a2b 100%)}
.hero__script{left:140px;top:145px;font-family:'Great Vibes',cursive;font-size:104px;color:var(--white);line-height:1}
.hero__sub{left:144px;top:275px;font-weight:700;font-size:23px;line-height:30px;color:var(--white);text-transform:uppercase}
.hero__arrow{width:32px;height:32px;border-radius:50%;background:rgba(255,255,255,.85)}

/* about */
.about__frame{left:158px;top:683px;width:452px;height:603px;border:4px solid var(--peach);box-shadow:6px 6px 0 rgba(0,0,0,.08)}
.about__photo{left:144px;top:683px;width:452px;height:593px;background:linear-gradient(160deg,#a2704f,#c99878 45%,#6b5a4c)}
.about__script{left:706px;top:822px;font-family:'Great Vibes',cursive;font-size:40px;color:var(--navy)}
.about__title{left:708px;top:866px;font-weight:700;font-size:31px;color:var(--navy)}
.about__body{left:660px;top:918px;width:400px;font-size:13.5px;line-height:24px;color:var(--ink)}

/* services */
.services{left:0;top:1389px;width:1200px;height:803px;background-color:var(--lavender);background-image:radial-gradient(#dcdbea 1px,transparent 1px);background-size:8px 8px}
.services .section-title{top:84px;color:var(--navy-deep)}
.svc{position:absolute;width:436px;height:247px;border-radius:24px;padding:36px 40px}
.svc--navy{background:var(--navy);color:var(--white)}
.svc--peach{background:var(--peach);color:var(--navy-deep)}
.svc__title{font-weight:700;font-size:15px;line-height:22px;text-transform:uppercase}
.svc__text{font-size:16px;line-height:22px;margin-top:14px}
.svc--right{text-align:right}
.svc .btn{width:128px;height:34px;font-size:12px;position:static;display:inline-flex;margin-top:18px}
.svc__badge{position:absolute;width:92px;height:92px;border-radius:50%;background:var(--white);padding:7px}
.svc__badge span{display:block;width:100%;height:100%;border-radius:50%}
.hub{left:480px;top:325px;width:226px;height:226px;border-radius:50%;background:var(--white);box-shadow:0 4px 14px rgba(0,0,0,.12)}
.hub__art{position:absolute;left:48px;top:48px;width:130px;height:130px;border-radius:50%;background:radial-gradient(circle at 45% 40%,#d9a48c,#3e6fa6)}

/* testimonials */
.quotes{left:0;top:2192px;width:1200px;height:741px}
.quotes .section-title{top:148px;color:var(--white)}
.quote-card{left:268px;top:261px;width:668px;height:284px;background:var(--white);border-radius:6px;box-shadow:0 6px 0 #ddd}
.quote-card__text{position:absolute;left:72px;top:32px;width:524px;text-align:center;font-size:14px;line-height:27px;color:var(--muted)}
.quote-card__name{position:absolute;left:160px;top:222px;font-size:13.5px;color:var(--muted)}
.quote-mark{position:absolute;font-family:Georgia,serif;font-size:54px;color:#e3e3e3;line-height:1}
.avatar{left:550px;top:476px;width:108px;height:108px;border-radius:50%;border:5px solid var(--white);background:linear-gradient(150deg,#7fa7c9,#34608f);box-shadow:0 2px 8px rgba(0,0,0,.25)}

/* feature icons */
.feature{position:absolute;top:3009px;width:220px;text-align:center}
.feature__ring{width:124px;height:124px;margin:0 auto;border-radius:50%;border:4px solid var(--peach);padding:8px;background:var(--white)}
.feature__ring span{display:block;width:100%;height:100%;border-radius:50%}
.feature__label{margin-top:20px;font-weight:700;font-size:16px;line-height:24px;text-transform:uppercase;color:var(--ink)}

/* benefited */
.benefit__photo{left:498px;top:3299px;width:558px;height:511px;background:linear-gradient(135deg,#d8dde2,#9ea5ac 50%,#5b6067)}
.benefit__box{left:144px;top:3344px;width:484px;height:402px;background:var(--white);border-left:4px solid var(--peach);border-top:4px solid var(--peach);padding:42px 18px 0 52px}
.benefit__title{font-weight:700;font-size:29px;line-height:38px;text-transform:uppercase;color:var(--ink)}
.benefit__body{margin-top:18px;font-size:13px;line-height:23px;color:var(--ink)}
.benefit__body p+p{margin-top:14px}

/* blog */
.blog{left:0;top:3935px;width:1200px;height:700px;background:var(--peach)}
.blog .section-title{top:80px;color:var(--ink)}
.post{position:absolute;top:185px;width:288px;height:393px;background:var(--white);box-shadow:0 2px 6px rgba(0,0,0,.1)}
.post__img{height:181px}
.post__title{margin:26px 20px 0;text-align:center;font-weight:700;font-size:14.5px;line-height:22px;text-transform:uppercase}
.post__date{margin-top:10px;text-align:center;font-weight:700;font-size:13.5px;color:var(--navy);display:flex;align-items:center;justify-content:center;gap:7px}
.post__text{margin:10px 22px 0;text-align:center;font-size:13px;line-height:21px;color:var(--muted)}

/* contact */
.contact{left:0;top:4580px;width:1200px;height:620px}
.contact .section-title{top:122px;color:var(--white)}
.info{position:absolute;left:144px;display:flex;gap:20px;color:var(--white)}
.info__icon{width:44px;height:44px;border-radius:50%;border:2px solid var(--white);display:flex;align-items:center;justify-content:center;flex-shrink:0}
.info__label{font-size:18px}
.info__value{font-size:16px;line-height:27px;max-width:230px}
.field{position:absolute;border:1px solid rgba(255,255,255,.7);font-size:13px;color:var(--white);padding:10px 12px}
.footer{left:0;top:5200px;width:1200px;height:100px;background:var(--navy-deep);color:var(--white);font-size:15px}
.social{position:absolute;top:34px;width:36px;height:36px;border-radius:50%;border:2px solid var(--white)}
</style>
</head>
<body>

<!-- top bar -->
<div class="abs topbar">
  <div class="topbar__item" style="left:355px">
    <svg width="14" height="14" viewBox="0 0 24 24"><path fill="#163a60" d="M6.6 10.8a15 15 0 006.6 6.6l2.2-2.2c.3-.3.7-.4 1-.2 1.1.4 2.3.6 3.6.6.6 0 1 .4 1 1V20c0 .6-.4 1-1 1A17 17 0 013 4c0-.6.4-1 1-1h3.5c.6 0 1 .4 1 1 0 1.3.2 2.5.6 3.6.1.3 0 .7-.2 1z"/></svg>
    Call +66 80 555 0142</div>
  <div class="topbar__item" style="left:585px">
    <svg width="16" height="12" viewBox="0 0 16 12"><rect width="16" height="12" fill="#163a60"/><path d="M0 0l8 6 8-6" stroke="#ebb6a2" fill="none"/></svg>
    clara@whitfieldva.org</div>
  <div class="topbar__item" style="left:786px">
    <svg width="14" height="14" viewBox="0 0 14 14"><circle cx="7" cy="7" r="7" fill="#163a60"/><path d="M7 3v4h3" stroke="#ebb6a2" stroke-width="1.6" fill="none"/></svg>
    Is now closed 9:00 am - 5:00 pm</div>
</div>

<!-- nav -->
<header class="abs nav">
  <div class="abs brand">
    <span class="brand__mark"></span>
    <div><div class="brand__name">Clara M Whitfield</div><div class="brand__tag">Virtual Assistant and Proofreader</div></div>
  </div>
  <nav class="abs nav__links"><span class="is-active">Home</span><span>Services</span><span>System Applications</span><span>Fees</span><span>Why Me?</span><span>Contact</span></nav>
</header>

<!-- hero -->
<section class="abs hero" role="img" aria-label="Photo of hands typing on a laptop at a café table with a coffee cup">
  <div class="abs hero__script">Allow me...</div>
  <div class="abs hero__sub">To handle the details so you can<br>get on with business.</div>
  <div class="btn btn--navy" style="left:144px;top:360px;width:156px;height:42px">Learn More</div>
  <div class="btn btn--peach" style="left:312px;top:360px;width:156px;height:42px">Contact</div>
  <svg class="abs hero__arrow" style="left:69px;top:281px" viewBox="0 0 32 32"><path d="M19 9l-7 7 7 7" stroke="#333" stroke-width="2.5" fill="none"/></svg>
  <svg class="abs hero__arrow" style="left:1099px;top:281px" viewBox="0 0 32 32"><path d="M13 9l7 7-7 7" stroke="#333" stroke-width="2.5" fill="none"/></svg>
</section>

<!-- about -->
<div class="abs about__frame"></div>
<div class="abs about__photo" role="img" aria-label="Portrait photo of the virtual assistant"></div>
<div class="abs about__script">about</div>
<div class="abs about__title">CLARA M WHITFIELD</div>
<p class="abs about__body">Every great leader is backed by diligent and knowledgeable support. Have you ever wondered what it would be like to have your very own personal assistant? Well, you can. A virtual assistant can do everything a full-time assistant can, with the added bonus that she can save you money. Whether you need daily help, or help with special assignments or big projects, hiring me as your VA will save you the costs typically associated with an employee holiday pay, sick pay, overtime, taxes, and insurance, are no longer your concern. And, as a virtual assistant, I only charge for the hours I actually work--no more resource-siphoning downtime.</p>
<div class="btn btn--navy" style="left:660px;top:1212px;width:156px;height:43px">Learn More</div>
<div class="btn btn--peach" style="left:829px;top:1212px;width:156px;height:43px">Contact</div>

<!-- services -->
<section class="abs services">
  <h2 class="section-title">Our Services</h2>
  <div class="svc svc--navy" style="left:158px;top:202px;padding-left:106px">
    <div class="svc__title">Organizational/Project<br>Management</div>
    <div class="svc__text">Reliable project and team management, master of organisation</div>
    <span class="btn btn--peach" style="color:#fff">Learn More</span>
  </div>
  <div class="svc svc--peach svc--right" style="left:603px;top:202px;padding-right:110px">
    <div class="svc__title">Website<br>Admininstration</div>
    <div class="svc__text">Dependable and reliable website updates like clockwork</div>
    <span class="btn btn--navy">Learn More</span>
  </div>
  <div class="svc svc--peach" style="left:158px;top:459px;padding-left:92px">
    <div class="svc__title">Administrative and<br>Accounting Support</div>
    <div class="svc__text">Work smarter not harder with the right VA by your side</div>
    <span class="btn btn--navy">Learn More</span>
  </div>
  <div class="svc svc--navy svc--right" style="left:603px;top:459px;padding-right:110px">
    <div class="svc__title">Editorial Service<br>Proofreading</div>
    <div class="svc__text">Catching simple typos and grammatical faux pas to preserve your integrity</div>
    <span class="btn btn--peach" style="color:#fff">Learn More</span>
  </div>
  <div class="svc__badge" style="left:152px;top:186px"><span role="img" aria-label="Project management icon" style="background:var(--navy)"></span></div>
  <div class="svc__badge" style="left:956px;top:186px"><span role="img" aria-label="Website icon" style="background:var(--peach)"></span></div>
  <div class="svc__badge" style="left:152px;top:636px"><span role="img" aria-label="Accounting icon" style="background:var(--peach)"></span></div>
  <div class="svc__badge" style="left:956px;top:636px"><span role="img" aria-label="Proofreading icon" style="background:var(--navy)"></span></div>
  <div class="abs hub"><div class="hub__art" role="img" aria-label="Illustration of a quill pen in an ink bottle"></div></div>
</section>

<!-- testimonials -->
<section class="abs quotes">
  <svg class="abs" style="left:0;top:0" width="1200" height="741">
    <rect width="1200" height="741" fill="var(--night)"/>
    <polygon points="0,0 1200,0 0,55" fill="var(--lavender)"/>
    <polygon points="0,0 330,0 0,55" fill="var(--peach)"/>
    <polygon points="1200,590 1200,741 0,741" fill="var(--peach)"/>
    <polygon points="1200,632 1200,741 0,741" fill="var(--white)"/>
  </svg>
  <div class="abs" style="left:0;top:55px;width:1200px;height:560px;background:linear-gradient(180deg,rgba(40,50,65,.55),rgba(20,26,36,.2))" role="img" aria-label="Dim background photo of a workspace"></div>
  <h2 class="section-title">Our Customers Say</h2>
  <svg class="abs" style="left:185px;top:370px" width="24" height="40"><path d="M18 4L6 20l12 16" stroke="#fff" stroke-width="3.5" fill="none"/></svg>
  <svg class="abs" style="left:995px;top:370px" width="24" height="40"><path d="M6 4l12 16L6 36" stroke="#fff" stroke-width="3.5" fill="none"/></svg>
  <div class="abs quote-card">
    <span class="quote-mark" style="left:86px;top:22px">&ldquo;</span>
    <p class="quote-card__text">Sed ut perspiciatis unde omnis iste natus error sit voluptatem accusantium doloremque laudantium, totam rem aperiam, eaque ipsa quae ab illo inventore veritatis et quasi architecto beatae vitae dicta sunt explicabo. Nemo enim ipsam voluptatem quia voluptas sit aspernatur aut odit aut fugit, sed quia consequuntur magni dolores eos qui ratione voluptatem sequi nesciunt.</p>
    <span class="quote-card__name">Mr. Halloway</span>
    <span class="quote-mark" style="left:415px;top:208px">&rdquo;</span>
  </div>
  <div class="abs avatar" role="img" aria-label="Client portrait photo"></div>
</section>

<!-- feature icons -->
<div class="feature" style="left:137px"><div class="feature__ring"><span style="background:var(--navy)" role="img" aria-label="Globe and team icon"></span></div><div class="feature__label">Why Me?</div></div>
<div class="feature" style="left:367px"><div class="feature__ring"><span style="background:var(--peach)" role="img" aria-label="Handshake and gears icon"></span></div><div class="feature__label">Who's Benefited<br>From My Help...</div></div>
<div class="feature" style="left:600px"><div class="feature__ring"><span style="background:var(--navy)" role="img" aria-label="Devices icon"></span></div><div class="feature__label">What I Can Do<br>For You...</div></div>
<div class="feature" style="left:833px"><div class="feature__ring"><span style="background:var(--navy)" role="img" aria-label="Person at desk icon"></span></div><div class="feature__label">Sometimes Your<br>Calling... Well,<br>It Finds You!</div></div>

<!-- who benefited -->
<div class="abs benefit__photo" role="img" aria-label="Top-down photo of a desk with laptop, keyboard, coffee and papers"></div>
<div class="abs benefit__box">
  <h3 class="benefit__title">Who's Benefited<br>From My Help...</h3>
  <div class="benefit__body">
    <p>My employers and clients hail from backgrounds in marketing, education, import/export businesses, IT, health and wellbeing and hospitality. They range from small to large businesses and individuals, all with a common issue they needed help managing the day-to-day details that make their operations run smoothly.</p>
    <p>My clients are entrepreneurs, consultants, charitable organisations, small businesses, students and professors all of whom can attest to the benefits of outsourcing time consuming tasks that distract them from their primary mission.</p>
  </div>
</div>

<!-- blog -->
<section class="abs blog">
  <h2 class="section-title">Latest Blog</h2>
  <article class="post" style="left:140px">
    <div class="post__img" role="img" aria-label="Photo of hands on a laptop" style="background:linear-gradient(135deg,#5d7d99,#23384f)"></div>
    <div class="post__title">Sed ut perspiciatis unde omnis iste natus</div>
    <div class="post__date"><svg width="12" height="12"><rect x="1" y="2" width="10" height="9" fill="none" stroke="#1d4c7c" stroke-width="1.6"/><rect x="1" y="2" width="10" height="3" fill="#1d4c7c"/></svg>September 4, 2020</div>
    <p class="post__text">Sed ut perspiciatis unde omnis iste natus error sit voluptatem accuntium doque laium, totam rem aperiam</p>
  </article>
  <article class="post" style="left:453px">
    <div class="post__img" role="img" aria-label="Photo of a hand touching digital gears" style="background:linear-gradient(135deg,#c9cdd2,#3d4249)"></div>
    <div class="post__title">Sed ut perspiciatis unde omnis iste natus</div>
    <div class="post__date"><svg width="12" height="12"><rect x="1" y="2" width="10" height="9" fill="none" stroke="#1d4c7c" stroke-width="1.6"/><rect x="1" y="2" width="10" height="3" fill="#1d4c7c"/></svg>September 4, 2020</div>
    <p class="post__text">Sed ut perspiciatis unde omnis iste natus error sit voluptatem accuntium doque laium, totam rem aperiam</p>
  </article>
  <article class="post" style="left:764px">
    <div class="post__img" role="img" aria-label="Photo of darts hitting a target" style="background:linear-gradient(135deg,#b7c3d6,#3e4f6b 60%,#b04450)"></div>
    <div class="post__title">Sed ut perspiciatis unde omnis iste natus</div>
    <div class="post__date"><svg width="12" height="12"><rect x="1" y="2" width="10" height="9" fill="none" stroke="#1d4c7c" stroke-width="1.6"/><rect x="1" y="2" width="10" height="3" fill="#1d4c7c"/></svg>September 4, 2020</div>
    <p class="post__text">Sed ut perspiciatis unde omnis iste natus error sit voluptatem accuntium doque laium, totam rem aperiam</p>
  </article>
</section>

<!-- contact -->
<section class="abs contact">
  <svg class="abs" style="left:0;top:0" width="1200" height="620">
    <defs><linearGradient id="contactBg" x1="0" y1="0" x2="1" y2="1"><stop offset="0" stop-color="#1f5587"/><stop offset="1" stop-color="#123a63"/></linearGradient></defs>
    <polygon points="0,0 1200,55 1200,620 0,620" fill="url(#contactBg)"/>
  </svg>
  <h2 class="section-title">Contact Us</h2>
  <div class="info" style="top:246px">
    <span class="info__icon"><svg width="18" height="22" viewBox="0 0 18 22"><path d="M9 1a7 7 0 00-7 7c0 5 7 13 7 13s7-8 7-13a7 7 0 00-7-7z" fill="none" stroke="#fff" stroke-width="2"/><circle cx="9" cy="8" r="2.5" fill="#fff"/></svg></span>
    <div><div class="info__label">Address:</div><div class="info__value">Clara M Whitfield 27B Elm Row<br>Maplewood, NV 40317</div></div>
  </div>
  <div class="info" style="top:342px">
    <span class="info__icon"><svg width="20" height="20" viewBox="0 0 24 24"><path fill="#fff" d="M6.6 10.8a15 15 0 006.6 6.6l2.2-2.2c.3-.3.7-.4 1-.2 1.1.4 2.3.6 3.6.6.6 0 1 .4 1 1V20c0 .6-.4 1-1 1A17 17 0 013 4c0-.6.4-1 1-1h3.5c.6 0 1 .4 1 1 0 1.3.2 2.5.6 3.6.1.3 0 .7-.2 1z"/></svg></span>
    <div><div class="info__label">Phone:</div><div class="info__value">+66 80 555 0142</div></div>
  </div>
  <div class="info" style="top:414px">
    <span class="info__icon"><svg width="20" height="20" viewBox="0 0 20 20"><circle cx="10" cy="10" r="4" fill="none" stroke="#fff" stroke-width="2"/><path d="M14 10v1.5a2 2 0 004 0V10a8 8 0 10-3 6.2" fill="none" stroke="#fff" stroke-width="2"/></svg></span>
    <div><div class="info__label">Email:</div><div class="info__value">info@clarawhitfield.com</div></div>
  </div>
  <div class="field" style="left:443px;top:250px;width:297px;height:40px">First Name</div>
  <div class="field" style="left:760px;top:250px;width:294px;height:40px">Mobile Number</div>
  <div class="field" style="left:443px;top:306px;width:297px;height:40px">Last Name</div>
  <div class="field" style="left:760px;top:306px;width:294px;height:40px">Email</div>
  <div class="field" style="left:443px;top:370px;width:611px;height:93px">Message</div>
  <div class="btn btn--peach" style="left:443px;top:487px;width:177px;height:41px">Submit</div>
</section>

<!-- footer -->
<footer class="abs footer">
  <div class="abs" style="left:144px;top:42px">Clara M Whitfield © 2020 All Rights Reserved | Privacy Policy</div>
  <span class="social" style="left:921px"></span>
  <span class="social" style="left:968px"></span>
  <span class="social" style="left:1018px"></span>
</footer>

</body>
</html>
```